I have a logo and need to design the business card and stationery.
Updates

The uploaded logo image named as GREYMARSH CONSTRUCTION which is to be replaced to GREYMARSH CONTRACTS. Kindly add below details and submit the designs- Company name- Greymarsh Engineering Contracts LLP Name & Post- Kelvan Joshi (Designated Partner) Address- Block No.317, Wing C, Tulvo Trade Court, Manek Pural Road, Ruparel Industrial Estate, Goregaon(E), Mumbai - 400 063 Contact- +91 97415 60382 Email- kelvanjoshi@mailbrook.example Website- www.greymarshcontracts.example Contact for Letterhead- +91-22-28754193

Hi Tovin Rahul, We are liking your Design #28860835. We have suggested some changes which are mentioned in feedback. Kindly revert with it asap to finalize this design.

Colors

Designer to choose colors to be used in the design.

```html
<!DOCTYPE html>
<html lang="en">
<head>
<meta charset="utf-8">
<title>Greymarsh Contracts – Business Card</title>
<link href="https://fonts.googleapis.com/css2?family=Urbanist:wght@400;500;700;800&display=swap" rel="stylesheet">
<style>
  :root{
    --backdrop:#c8c5c2;
    --paper:#f1f1f0;
    --ink:#141414;
    --text-light:#d6d6d6;
    --text-muted:#b5b5b5;
  }
  *{margin:0;padding:0;box-sizing:border-box}
  html,body{width:1200px;height:1014px;overflow:hidden}
  body{background:var(--backdrop);font-family:"Urbanist",sans-serif;position:relative}
  .card{position:absolute;left:337px;width:525px;height:292px;background:var(--paper);overflow:hidden;box-shadow:0 6px 18px rgba(0,0,0,.18)}
  .card--back{top:191px}
  .card--front{top:499px}
  .band{position:absolute;left:0;right:0;bottom:0;background:var(--ink)}
  .card--back .band{top:146px}
  .card--front .band{top:150px}
  .notch{position:absolute;top:0;background:var(--paper);display:flex;flex-direction:column;align-items:center}
  .card--back .notch{left:184px;width:157px;height:217px;padding-top:66px}
  .card--front .notch{left:117px;width:289px;height:176px;padding-top:48px}
  .brand-mark{background:var(--ink)}
  .card--back .brand-mark{width:84px;height:84px;margin-bottom:10px}
  .card--front .brand-mark{width:76px;height:76px;margin-bottom:8px}
  .brand-name{color:var(--ink);font-weight:800;text-align:center;line-height:1.05;text-transform:uppercase}
  .card--back .brand-name{font-size:15px;letter-spacing:.04em}
  .card--front .brand-name{font-size:20px;letter-spacing:.05em}
  .brand-name span{display:block}
  .brand-name .sub{letter-spacing:.32em;margin-right:-.32em}
  .address{position:absolute;left:0;right:0;top:228px;text-align:center;color:var(--text-light);font-size:12px;line-height:1.3}
  .person{position:absolute;right:309px;top:200px;text-align:right;color:var(--text-light)}
  .person-name{font-size:20px;font-weight:400;line-height:1}
  .person-name b{font-weight:700}
  .person-role{font-size:12px;color:var(--text-muted);margin-top:3px}
  .contacts{position:absolute;left:229px;top:193px;list-style:none;color:var(--text-light);font-size:12.5px}
  .contacts li{display:flex;align-items:center;gap:7px;height:18.5px}
  .contacts svg{width:11px;height:11px;flex:none}
</style>
</head>
<body>
  <section class="card card--back">
    <div class="band"></div>
    <div class="notch">
      <div class="brand-mark"></div>
      <div class="brand-name"><span>Greymarsh</span><span class="sub">Contracts</span></div>
    </div>
    <p class="address">Block No.317, Wing C, Tulvo Trade Court, Manek Pural<br>Road, Ruparel Industrial Estate, Goregaon(E), Mumbai - 400 063</p>
  </section>

  <section class="card card--front">
    <div class="band"></div>
    <div class="notch">
      <div class="brand-mark"></div>
      <div class="brand-name"><span>Greymarsh</span><span class="sub">Contracts</span></div>
    </div>
    <div class="person">
      <p class="person-name"><b>Kelvan</b> Joshi</p>
      <p class="person-role">(Designated Partner)</p>
    </div>
    <ul class="contacts">
      <li><svg viewBox="0 0 12 12"><circle cx="6" cy="6" r="6" fill="#d6d6d6"/><path d="M4 3.2l1 1.3-.6.8c.4.9 1.1 1.6 2 2l.8-.6 1.3 1-.6 1c-2.4-.3-4.2-2.1-4.5-4.5z" fill="#141414"/></svg>+91 97415 60382</li>
      <li><svg viewBox="0 0 12 12"><circle cx="6" cy="6" r="6" fill="#d6d6d6"/><rect x="3" y="4" width="6" height="4.2" fill="#141414"/><path d="M3 4l3 2.3L9 4" stroke="#d6d6d6" stroke-width=".7" fill="none"/></svg>kelvanjoshi@mailbrook.example</li>
      <li><svg viewBox="0 0 12 12"><circle cx="6" cy="6" r="6" fill="#d6d6d6"/><circle cx="6" cy="6" r="3.4" fill="none" stroke="#141414" stroke-width=".8"/><ellipse cx="6" cy="6" rx="1.4" ry="3.4" fill="none" stroke="#141414" stroke-width=".7"/><path d="M2.6 6h6.8" stroke="#141414" stroke-width=".7"/></svg>www.greymarshcontracts.example</li>
    </ul>
  </section>
</body>
</html>
```